Enterprise image desing

The designs are for a fashion store for young men and women.
Updates

Los diseƱos parecen similares

Target Market(s)

Young

Font styles to use
Sans Serif

Colors
ec1f27
ffffff
1b1b1b

Requirements
Must have
• Use clean and modern sources
Nice to have
• n / a
Should not have
• n / a

```html
<!DOCTYPE html>
<html lang="en">
<head>
<meta charset="utf-8">
<title>Veltrano Stationery</title>
<link href="https://fonts.googleapis.com/css2?family=Lato:wght@400;700;900&family=Playfair+Display:ital@1&display=swap" rel="stylesheet">
<style>
:root{
  --navy:#1b2852;
  --red:#d7232e;
  --white:#ffffff;
  --ink:#1b1b1b;
  --stage:#c8c8c8;
  --pink:#f7dcdf;
  --grey:#e2e3e7;
}
*{margin:0;padding:0;box-sizing:border-box}
html,body{width:1200px;height:1200px;overflow:hidden;background:var(--stage);font-family:"Lato",sans-serif;color:var(--ink)}
.canvas{position:relative;width:1200px;height:1200px}
.sheet{position:absolute;background:var(--white);overflow:hidden;box-shadow:3px 3px 2px rgba(0,0,0,.45)}
.brand{display:flex;align-items:center;font-weight:900;color:var(--navy);letter-spacing:.02em;white-space:nowrap}
.brand-dot{background:var(--red);display:inline-block;flex:none}
.on-navy .brand{color:var(--white)}
.on-navy .brand-dot{background:var(--white)}

/* cards */
.card-front-navy{left:62px;top:50px;width:335px;height:192px;background:var(--navy)}
.card-front-white{left:445px;top:51px;width:335px;height:192px}
.card-front .brand{position:absolute;left:0;right:0;top:0;bottom:0;justify-content:center;font-size:38px;gap:12px}
.card-front .brand-dot{width:30px;height:30px}

.card-back-left{left:60px;top:271px;width:335px;height:192px}
.card-back-right{left:440px;top:270px;width:336px;height:192px}
.person-name{font-size:13px;color:var(--navy)}
.person-role{font-size:9px;color:var(--ink);margin-top:1px}
.card-back-right .person-name{color:var(--red)}
.holder{position:absolute}
.contact{font-size:11px;color:var(--ink);line-height:14px;display:flex;align-items:center;gap:5px}
.contact .ic{width:10px;height:10px;flex:none}
.gap{height:8px}
.addr{font-size:11px;line-height:14px;color:var(--ink)}
.divider{position:absolute;left:188px;top:72px;width:1.5px;height:97px;background:var(--red)}
.card-back-left .brand{position:absolute;left:22px;top:147px;font-size:18px;gap:6px}
.card-back-left .brand-dot{width:14px;height:14px}
.corner-block{position:absolute;background:var(--red);border-top-left-radius:30px}
.card-back-right .corner-block{left:212px;top:68px;width:124px;height:124px}

/* letterhead */
.letterhead{left:97px;top:519px;width:440px;height:622px}
.letterhead .brand{position:absolute;left:0;right:0;top:30px;justify-content:center;font-size:21px;gap:7px}
.letterhead .brand-dot{width:16px;height:16px}
.letter-body{position:absolute;left:38px;top:90px;width:365px;font-size:8px;line-height:15.6px;color:var(--ink)}
.letter-to{font-weight:700;margin-bottom:15px;font-size:7.4px}
.letter-body p{margin-bottom:15.6px}
.signature{width:95px;height:40px;background:#eeeeee;border-radius:2px;margin:2px 0 2px}
.faint-block{position:absolute;background:var(--pink);border-top-left-radius:46px}
.letterhead .faint-block{left:267px;top:449px;width:173px;height:173px}
.footer-rule{position:absolute;left:43px;top:588px;width:353px;height:1.5px;background:var(--navy)}
.footer-row{position:absolute;left:43px;top:596px;width:370px;display:flex;justify-content:space-between;font-size:5.6px;color:var(--ink)}
.footer-row span{display:flex;align-items:center;gap:3px}
.footer-row .ic{width:7px;height:7px}

/* envelopes */
.envelope-front{left:580px;top:523px;width:460px;height:189px}
.envelope-front .brand{position:absolute;left:14px;top:12px;font-size:12px;gap:4px}
.envelope-front .brand-dot{width:10px;height:10px}
.return-addr{position:absolute;left:14px;top:30px;font-size:7px;line-height:9.5px;color:#555}
.envelope-front .faint-block{left:348px;top:76px;width:112px;height:113px;border-top-left-radius:36px}
.envelope-back{left:580px;top:738px;width:462px;height:190px}
.envelope-back svg{position:absolute;left:0;top:0}

/* compliment slip */
.comp-slip{left:590px;top:961px;width:386px;height:160px}
.comp-slip .brand{position:absolute;left:12px;top:12px;font-size:10px;gap:4px}
.comp-slip .brand-dot{width:8px;height:8px}
.comp-note{position:absolute;right:22px;top:136px;font-family:"Playfair Display",serif;font-style:italic;font-size:12.5px;color:var(--navy)}
</style>
</head>
<body>
<div class="canvas">

  <section class="sheet card-front card-front-navy on-navy">
    <div class="brand"><span class="brand-dot"></span>VELTRANO</div>
  </section>

  <section class="sheet card-front card-front-white">
    <div class="brand"><span class="brand-dot"></span>VELTRANO</div>
  </section>

  <section class="sheet card-back-left">
    <div class="holder" style="left:22px;top:19px">
      <div class="person-name">Daniel Vorne</div>
      <div class="person-role">Director</div>
    </div>
    <div class="divider"></div>
    <div class="holder" style="left:202px;top:67px">
      <div class="contact"><svg class="ic" viewBox="0 0 10 10"><circle cx="5" cy="5" r="5" fill="#d7232e"/><rect x="3.3" y="2" width="3.4" height="6" rx=".6" fill="#fff"/></svg>123-555-0147</div>
      <div class="contact"><svg class="ic" viewBox="0 0 10 10"><circle cx="5" cy="5" r="5" fill="#d7232e"/><rect x="2.5" y="3.5" width="5" height="3.5" rx=".8" fill="#fff"/></svg>123-555-0198</div>
      <div class="gap"></div>
      <div class="contact"><svg class="ic" viewBox="0 0 10 10"><circle cx="5" cy="5" r="5" fill="#d7232e"/><rect x="2.5" y="3.2" width="5" height="3.6" fill="#fff"/></svg>hello@veltrano.com</div>
      <div class="contact"><svg class="ic" viewBox="0 0 10 10"><circle cx="5" cy="5" r="5" fill="#d7232e"/><circle cx="5" cy="5" r="2.6" fill="none" stroke="#fff" stroke-width=".8"/></svg>www.veltrano.com</div>
      <div class="gap" style="height:6px"></div>
      <div class="addr">000 Harbor Street<br>WA 30000,xxxxxxx</div>
    </div>
    <div class="brand"><span class="brand-dot"></span>VELTRANO</div>
  </section>

  <section class="sheet card-back-right">
    <div class="holder" style="left:30px;top:24px">
      <div class="person-name">Daniel Vorne</div>
      <div class="person-role">Director</div>
    </div>
    <div class="holder" style="left:30px;top:70px">
      <div class="contact"><svg class="ic" viewBox="0 0 10 10"><circle cx="5" cy="5" r="5" fill="#d7232e"/><rect x="3.3" y="2" width="3.4" height="6" rx=".6" fill="#fff"/></svg>123-555-0147</div>
      <div class="contact"><svg class="ic" viewBox="0 0 10 10"><circle cx="5" cy="5" r="5" fill="#d7232e"/><rect x="2.5" y="3.5" width="5" height="3.5" rx=".8" fill="#fff"/></svg>123-555-0198</div>
      <div class="gap"></div>
      <div class="contact"><svg class="ic" viewBox="0 0 10 10"><circle cx="5" cy="5" r="5" fill="#d7232e"/><rect x="2.5" y="3.2" width="5" height="3.6" fill="#fff"/></svg>hello@veltrano.com</div>
      <div class="contact"><svg class="ic" viewBox="0 0 10 10"><circle cx="5" cy="5" r="5" fill="#d7232e"/><circle cx="5" cy="5" r="2.6" fill="none" stroke="#fff" stroke-width=".8"/></svg>www.veltrano.com</div>
      <div class="gap" style="height:6px"></div>
      <div class="addr">000 Harbor Street<br>WA 30000,xxxxxxx</div>
    </div>
    <div class="corner-block"></div>
  </section>

  <section class="sheet letterhead">
    <div class="faint-block"></div>
    <div class="brand"><span class="brand-dot"></span>VELTRANO</div>
    <div class="letter-body">
      <div class="letter-to">To<br>Lorem Ipsum is simply<br>Lorem Ipsum is Lorem Ipsum is<br>Lorem Ipsum is</div>
      <p>dummy text of the printing and typesetting industry. Lorem Ipsum has been the industry's standard dummy text ever since the 1500s, when an unknown printer took a galley of type and scrambled it to make a type specimen book. It has survived not only five centuries, but also the leap into electronic typesetting, remaining essentially unchanged.</p>
      <p>It is a long established fact that a reader will be distracted by the readable content of a page when looking at its layout. The point of using Lorem Ipsum is that it has a more-or-less normal distribution of letters, as opposed to using 'Content here, content here', making it look like readable English. Many desktop publishing packages and web page editors now use Lorem Ipsum as their default model text, and a search for 'lorem .</p>
      <p>Contrary to popular belief, Lorem Ipsum is not simply random text. It has roots in a piece of classical Latin literature from 45 BC, making it over 2000 years old. Ronald Mertenson, a Latin professor at Westbrook-Lowell College in Vermont, looked up one of the more obscure Latin words, consectetur, from a Lorem Ipsum passage,</p>
      <div>Lorem Ipsum</div>
      <div class="signature" role="img" aria-label="Handwritten signature"></div>
      <div>Lorem Ipsum is a dummy</div>
    </div>
    <div class="footer-rule"></div>
    <div class="footer-row">
      <span><svg class="ic" viewBox="0 0 10 10"><circle cx="5" cy="5" r="5" fill="#d7232e"/></svg>123-555-0147</span>
      <span><svg class="ic" viewBox="0 0 10 10"><circle cx="5" cy="5" r="5" fill="#d7232e"/></svg>123-555-0198</span>
      <span><svg class="ic" viewBox="0 0 10 10"><circle cx="5" cy="5" r="5" fill="#d7232e"/></svg>hello@veltrano.com</span>
      <span><svg class="ic" viewBox="0 0 10 10"><circle cx="5" cy="5" r="5" fill="#d7232e"/></svg>www.veltrano.com</span>
    </div>
  </section>

  <section class="sheet envelope-front">
    <div class="faint-block"></div>
    <div class="brand"><span class="brand-dot"></span>VELTRANO</div>
    <div class="return-addr">000 Harbor Street<br>WA 30000,xxxxxxx</div>
  </section>

  <section class="sheet envelope-back">
    <svg width="462" height="190" viewBox="0 0 462 190">
      <path d="M0 0 L30 66 Q33 71 40 71 L422 71 Q429 71 432 66 L462 0" fill="none" stroke="#8a8a8a" stroke-width="1"/>
    </svg>
  </section>

  <section class="sheet comp-slip">
    <div class="brand"><span class="brand-dot"></span>VELTRANO</div>
    <div class="comp-note">With Compliments</div>
  </section>

</div>
</body>
</html>
```